Business card for medical clinic

I need an upmarket, modern medical/health business card for my clinic

Contact Information for Business Card

name, address, email, qr code

```html
<!DOCTYPE html>
<html lang="en">
<head>
<meta charset="utf-8">
<title>Corvale Health Partners – Business Card</title>
<link rel="stylesheet" href="https://fonts.googleapis.com/css2?family=Marcellus&family=Arimo:wght@400;500&display=swap">
<style>
  :root{
    --page:#23272d;
    --navy:#16284a;
    --navy-deep:#122042;
    --blue:#2aa7df;
    --blue-mid:#1f6fa3;
    --ink-blue:#1b63a8;
    --white:#ffffff;
    --text-dark:#2b2f36;
  }
  *{margin:0;padding:0;box-sizing:border-box}
  html,body{width:1200px;height:900px;overflow:hidden;background:var(--page)}
  .canvas{width:1200px;height:900px;display:flex;flex-direction:column;align-items:center;justify-content:center;gap:32px}
  .card{position:relative;width:680px;height:389px;border-radius:26px;overflow:hidden;box-shadow:0 14px 30px rgba(0,0,0,.45)}

  /* Front */
  .card-front{background:var(--white)}
  .card-front .waves{position:absolute;inset:0;width:100%;height:100%}
  .brand{position:absolute;display:flex;align-items:center;gap:12px;font-family:"Marcellus",serif;letter-spacing:.08em;text-transform:uppercase}
  .card-front .brand{left:40px;top:38px;color:var(--ink-blue);font-size:21px}
  .brand-dot{width:34px;height:34px;border-radius:50%;border:3px solid currentColor;flex:none}
  .holder{position:absolute;right:40px;top:108px;text-align:right}
  .holder-name{font-family:"Marcellus",serif;font-size:29px;letter-spacing:.06em;color:var(--ink-blue);text-transform:uppercase;line-height:1.2}
  .holder-role{font-family:"Arimo",sans-serif;font-size:15px;color:var(--text-dark);margin-top:2px}
  .contact{position:absolute;right:34px;bottom:22px;list-style:none;font-family:"Arimo",sans-serif;color:var(--white);font-size:15px;line-height:22px;text-align:right}
  .contact li{display:flex;align-items:center;justify-content:flex-end;gap:8px}
  .contact li.plain{padding-right:22px}
  .contact svg{width:14px;height:14px;flex:none}

  /* Back */
  .card-back{background:linear-gradient(35deg,var(--blue) 0%,var(--blue-mid) 35%,var(--navy) 70%,var(--navy-deep) 100%)}
  .card-back .brand{left:50%;top:50%;transform:translate(-50%,-50%);color:var(--white);font-size:30px;white-space:nowrap;gap:16px}
  .card-back .brand-dot{width:46px;height:46px}
</style>
</head>
<body>
<main class="canvas">

  <section class="card card-front" aria-label="Card front">
    <svg class="waves" viewBox="0 0 680 389" preserveAspectRatio="none" aria-hidden="true">
      <defs>
        <linearGradient id="bandFill" x1="0" y1="0" x2="1" y2="1">
          <stop offset="0" stop-color="#16284a"/>
          <stop offset=".55" stop-color="#1d4f82"/>
          <stop offset="1" stop-color="#2aa7df"/>
        </linearGradient>
      </defs>
      <path d="M0 120 C80 190 200 202 340 204 C480 206 600 206 680 232 L680 389 L0 389 Z" fill="url(#bandFill)"/>
      <path d="M0 98 C80 170 200 186 340 190 C480 193 600 194 680 218" fill="none" stroke="#2aa7df" stroke-width="6"/>
      <path d="M60 170 C150 196 260 198 380 198 C480 199 560 202 640 214" fill="none" stroke="#16284a" stroke-width="3"/>
      <path d="M420 198 C520 200 600 206 676 226" fill="none" stroke="#ffffff" stroke-width="2"/>
    </svg>

    <div class="brand"><span class="brand-dot"></span>Corvale Health Partners</div>

    <div class="holder">
      <div class="holder-name">Daniel Hart</div>
      <div class="holder-role">Director/Founder</div>
    </div>

    <ul class="contact">
      <li class="plain">318 Harbor Lane</li>
      <li class="plain">Westfield CA 90215</li>
      <li>0317 482 9060
        <svg viewBox="0 0 16 16" aria-hidden="true"><circle cx="8" cy="8" r="8" fill="#fff"/><path d="M5 4.5c.6-.4 1.2 0 1.4.6l.4 1c.1.4-.1.7-.4.9l-.4.3c.4.9 1.1 1.6 2 2l.3-.4c.2-.3.6-.5.9-.4l1 .4c.6.2 1 .8.6 1.4-.5.8-1.4 1.1-2.3.7C6.7 10.3 5.7 9.3 5 7.5c-.4-1 0-2.4 0-3z" fill="#1d4f82"/></svg>
      </li>
      <li>info@corvalehealth.com
        <svg viewBox="0 0 16 16" aria-hidden="true"><circle cx="8" cy="8" r="8" fill="#fff"/><rect x="4" y="5.2" width="8" height="5.6" rx=".6" fill="#1d4f82"/><path d="M4.3 5.6 8 8.4l3.7-2.8" fill="none" stroke="#fff" stroke-width=".9"/></svg>
      </li>
      <li>www.corvalehealth.com
        <svg viewBox="0 0 16 16" aria-hidden="true"><circle cx="8" cy="8" r="8" fill="#fff"/><circle cx="8" cy="8" r="4.2" fill="none" stroke="#1d4f82" stroke-width="1"/><ellipse cx="8" cy="8" rx="1.8" ry="4.2" fill="none" stroke="#1d4f82" stroke-width="1"/><path d="M3.8 8h8.4" stroke="#1d4f82" stroke-width="1"/></svg>
      </li>
    </ul>
  </section>

  <section class="card card-back" aria-label="Card back">
    <div class="brand"><span class="brand-dot"></span>Corvale Health Partners</div>
  </section>

</main>
</body>
</html>
```